Professional violinist needs business cards

I am trying to attract the following jobs:
-private violin lessons (primarily classical)
-performance gigs (weddings, birthday parties, funerals, etc.)
-collaborations with other artists (studio recordings, performances)

I want to communicate that I have a very high standard of excellence for my work, but I also love people and celebrations.
Values/style words I like are:
love, joy, peace, fun, beauty, authenticity, excellence, warmth, refined/sleek, free spirited. If that's too confusing, just ignore :)

I will attach my favorite business card template that I could find on Canva. The lines are supposed to be like a music staff, which I think is really cool, but I also don't want it to look too busy. I like the simple black and white--I think it looks sharp--but I also am open to other ideas. I also have seen business cards with pictures included that looked great, so I attached an image that could be used as well.

I am also attaching a file that I made of my initials that could be used as a logo, but I'm not sure if it should be included.

Information on the card:
-My name (18 letters total)
-"violinist"
-phone number, email, website

Thank you!

```html
<!DOCTYPE html>
<html lang="en">
<head>
<meta charset="utf-8">
<title>Elena Marlowe · Violinist · Business Cards</title>
<link rel="stylesheet" href="https://fonts.googleapis.com/css2?family=Raleway:wght@400;500;600&family=Arimo:wght@400&display=swap">
<style>
  :root {
    --canvas: #2a2a2a;
    --card-black: #050505;
    --card-white: #ffffff;
    --staff-line: #ffffff;
    --gold: #c8952c;
    --ink: #1a1a1a;
    --muted-ink: #333333;
    --photo-dark: #0b0b0b;
    --photo-warm: #3a2418;
  }
  * { box-sizing: border-box; margin: 0; padding: 0; }
  html, body {
    width: 1200px;
    height: 900px;
    overflow: hidden;
    background: var(--canvas);
  }
  .canvas {
    position: relative;
    width: 1200px;
    height: 900px;
  }
  .card {
    position: absolute;
    left: 250px;
    width: 700px;
    height: 400px;
    overflow: hidden;
    box-shadow: 0 10px 30px rgba(0,0,0,0.5);
  }

  /* Front: black card with music staff */
  .card-front {
    top: 30px;
    background: var(--card-black);
  }
  .staff {
    position: absolute;
    inset: 0;
  }
  .wordmark {
    position: absolute;
    left: 40px;
    top: 150px;
    font-family: "Raleway", sans-serif;
    font-weight: 600;
    font-size: 72px;
    line-height: 1;
    color: var(--staff-line);
    background: var(--card-black);
    padding: 4px 14px 10px 8px;
    letter-spacing: 1px;
  }
  .front-web {
    position: absolute;
    right: 34px;
    top: 306px;
    font-family: "Raleway", sans-serif;
    font-weight: 500;
    font-size: 14px;
    line-height: 1;
    letter-spacing: 1.5px;
    color: var(--staff-line);
  }

  /* Back: white card with portrait and contacts */
  .card-back {
    top: 470px;
    background: var(--card-white);
  }
  .portrait {
    position: absolute;
    left: 0;
    top: 0;
    width: 290px;
    height: 400px;
    background:
      radial-gradient(ellipse 45% 55% at 60% 60%, var(--photo-warm) 0%, rgba(58,36,24,0) 70%),
      var(--photo-dark);
  }
  .contact-block {
    position: absolute;
    left: 330px;
    top: 190px;
  }
  .name {
    font-family: "Raleway", sans-serif;
    font-weight: 500;
    font-size: 32px;
    color: var(--gold);
    letter-spacing: 0.5px;
  }
  .role {
    font-family: "Arimo", sans-serif;
    font-size: 14px;
    color: var(--muted-ink);
    margin-top: 2px;
  }
  .details {
    list-style: none;
    margin-top: 28px;
    font-family: "Arimo", sans-serif;
    font-size: 17px;
    line-height: 1.45;
    color: var(--ink);
  }
  .details .label {
    color: var(--gold);
  }
</style>
</head>
<body>
<main class="canvas">

  <section class="card card-front" aria-label="Card front">
    <svg class="staff" width="700" height="400" viewBox="0 0 700 400" aria-hidden="true">
      <g stroke="var(--staff-line)" stroke-width="3">
        <line x1="0" y1="60"  x2="700" y2="60"/>
        <line x1="0" y1="130" x2="700" y2="130"/>
        <line x1="0" y1="200" x2="700" y2="200"/>
        <line x1="0" y1="270" x2="700" y2="270"/>
        <line x1="0" y1="340" x2="700" y2="340"/>
      </g>
    </svg>
    <div class="wordmark">Elena Marlowe</div>
    <div class="front-web">www.elenamarlowe.com</div>
  </section>

  <section class="card card-back" aria-label="Card back">
    <div class="portrait" role="img" aria-label="Portrait photo of the violinist in a black dress holding her violin and bow, on a black background"></div>
    <div class="contact-block">
      <h1 class="name">Elena Marlowe</h1>
      <p class="role">Violinist</p>
      <ul class="details">
        <li><span class="label">phone:</span> 020 7946 0381</li>
        <li><span class="label">email:</span> hello@elenamarlowe.com</li>
        <li><span class="label">web:</span> www.elenamarlowe.com</li>
      </ul>
    </div>
  </section>

</main>
</body>
</html>
```